Qorvith Global Compounding Pharmacy needs a great Sales Brochure targeting doctors

We need a sales brochure that is catered to Physicians that will get their interest to use our services as a compounding pharmacy for their patients with the following--

Features: Qorvith is a compounding lab that provides customized solutions to doctors looking to improve the lives of their patients.

Advantages: We offer personalized service, quality products, and reliable pharmaceuticals.

Benefits: By working directly with us, we can create solutions that best meet your practice's needs.

The logo is provided as well as pictures and a design brief. Colors should reflect our site and be blue and/shades of blue

Design Brief has been uploaded as a PDF

Target Market(s)

Doctors

Industry/Entity Type

Healthcare Compounding Pharmacy

Colors
0054AA
0677BA
7BADD7
CADEEF
E8F1F8
0094D4
00A9DD
6FCCEA
C7EBF8
E9F6FB

Requirements
Must have
• This should be a bi-fold brochure Use the slogan from QORVITH INTRO in the brief and highlight it. The doctors need to be focus on why Qorvith is the right choice as well from the ABOUT QORVITH SECTION.
Nice to have
• I want to see the INTRO QORVITH paragraphs used. The main slogan to doctors is: Qorvith Global Compounding Pharmacy: The Right Choice The right choice for you and your Patients.
Should not have
• Don't use pictures Qorvith_420 and Qorvith_408. I have deleted both pictures from the brief

```html
<!DOCTYPE html>
<html lang="en">
<head>
<meta charset="utf-8">
<title>Qorvith Global Compounding Pharmacy – Brochure</title>
<link href="https://fonts.googleapis.com/css2?family=Rubik:wght@400;500;700&family=Open+Sans:wght@400;600&family=Roboto+Condensed:wght@400;700&family=Tinos&display=swap" rel="stylesheet">
<style>
:root{
  --navy:#111f8f;
  --navy-deep:#0b1673;
  --teal:#1fbf9b;
  --teal-light:#4fd6b4;
  --paper:#f3f4f6;
  --paper-shade:#e2e4e8;
  --ink:#2b2f3a;
  --board:#a7a7a7;
  --white:#ffffff;
}
*{box-sizing:border-box;margin:0;padding:0}
html,body{width:1200px;height:2389px;overflow:hidden}
body{background:var(--board);position:relative;font-family:"Open Sans",sans-serif;color:var(--ink)}

/* ---------- shared page ---------- */
.page{position:absolute;width:480px;height:700px;background:linear-gradient(90deg,var(--paper) 0%,var(--white) 50%,var(--paper-shade) 100%);overflow:hidden;box-shadow:0 4px 14px rgba(0,0,0,.3)}
.page-geo{position:absolute;left:0;top:0}
.brand{position:absolute;font-family:"Rubik",sans-serif;font-weight:400;letter-spacing:3px;color:#1b1b22}
.photo{position:absolute;left:0;top:0;width:100%;height:100%}
.page-foot{position:absolute;left:0;bottom:0;width:100%;height:45px;background:linear-gradient(90deg,var(--white),var(--paper-shade))}
.url{position:absolute;left:34px;top:10px;font-family:"Open Sans",sans-serif;font-size:13px;letter-spacing:4.2px;color:#1b1b22}
.url-bar{position:absolute;left:34px;bottom:0;width:180px;height:5px;background:var(--teal)}

/* ---------- cover ---------- */
.cover .photo{background:linear-gradient(135deg,#dfe6ec 0%,#b8c3cc 40%,#8a9aa8 70%,#c9d2da 100%);clip-path:polygon(171px 102px,480px 102px,480px 150px,402px 450px,0 450px)}
.cover .brand{right:28px;top:38px;font-size:38px}
.cover-band{position:absolute;left:0;top:450px;width:100%;height:205px;background:var(--navy)}
.cover-title{position:absolute;left:33px;top:26px;font-family:"Rubik",sans-serif;font-weight:700;font-size:33px;line-height:42px;color:var(--white)}
.cover-title .accent{color:var(--teal)}
.tagline{position:absolute;left:33px;top:140px;padding-left:14px;border-left:3px solid var(--teal);font-size:12.5px;line-height:18px;color:var(--white)}

/* ---------- back ---------- */
.back-head{position:absolute;left:0;top:0;width:100%;height:105px;background:linear-gradient(90deg,var(--teal),var(--teal-light))}
.back-head h2{position:absolute;left:50px;top:20px;font-family:"Rubik",sans-serif;font-weight:500;font-size:23px;color:var(--white)}
.back-head p{position:absolute;left:50px;top:52px;font-size:11px;line-height:15px;color:var(--white)}
.back-head .rule{position:absolute;left:34px;top:24px;width:3px;height:64px;background:var(--white)}
.back .photo{background:linear-gradient(160deg,#e9edf2 0%,#c9d3de 50%,#aebbc9 100%);clip-path:polygon(378px 128px,480px 128px,480px 245px,398px 440px,288px 440px)}
.intro-copy{position:absolute;left:35px;top:128px;width:360px;font-size:8.6px;line-height:14px;color:var(--ink)}
.intro-copy p+p{margin-top:14px}
.contact{position:absolute;left:35px;top:492px;color:var(--white);font-size:12.5px;line-height:16px}
.contact-icons{display:flex;gap:4px;margin-bottom:6px}
.contact-icons span{width:10px;height:10px;border-radius:50%;border:2px solid var(--white)}
.back .brand{left:292px;top:500px;font-size:28px;color:var(--white)}
.follow{position:absolute;left:298px;top:553px;display:flex;align-items:center;gap:8px;font-family:"Rubik",sans-serif;font-weight:500;font-size:13px;color:var(--teal)}
.follow .social{width:17px;height:17px;border-radius:50%;border:2px solid var(--white)}
.follow .social:first-of-type{margin-left:6px}
.contact-us{position:absolute;left:32px;top:598px;font-family:"Rubik",sans-serif;font-weight:500;font-size:60px;line-height:60px;letter-spacing:1px;color:transparent;-webkit-text-stroke:1.4px #2a45e6}

/* ---------- outer spread (top) ---------- */
.outer-spread{position:absolute;left:158px;top:40px;width:960px;height:700px;transform:scale(.92);transform-origin:0 0}
.outer-spread .page{top:0;box-shadow:none}
.outer-spread .back{left:0}
.outer-spread .cover{left:480px}
.outer-shadow{position:absolute;left:158px;top:40px;width:883px;height:644px;box-shadow:0 8px 22px rgba(0,0,0,.35)}
.caption{position:absolute;top:735px;font-family:"Tinos",serif;font-size:24px;color:#1b1b22}

/* ---------- inner spread ---------- */
.inner-spread{position:absolute;left:101px;top:1543px;width:1000px;height:757px;box-shadow:0 6px 18px rgba(0,0,0,.3)}
.inner-spread .page{top:0;width:500px;height:757px;box-shadow:none}
.inner-left{left:0}
.inner-right{left:500px;background:linear-gradient(90deg,var(--paper-shade) 0%,var(--white) 15%,var(--paper) 100%)}
.about-block{position:absolute;left:0;top:0;width:500px;height:264px;background:var(--navy);clip-path:polygon(0 0,360px 0,280px 264px,0 264px)}
.about-photo{background:linear-gradient(150deg,#cfe0ee 0%,#8fb2d4 45%,#dbe6ef 100%);clip-path:polygon(360px 0,500px 0,500px 264px,280px 264px)}
.services-photo{background:linear-gradient(160deg,#9ea7b0 0%,#d7dde3 50%,#7f8a95 100%);clip-path:polygon(284px 268px,500px 268px,500px 415px,262px 415px)}
.section-title{position:absolute;font-family:"Rubik",sans-serif;font-weight:700;font-size:25px;line-height:28px;padding-left:14px;border-left:3px solid currentColor}
.on-navy{color:var(--teal)}
.on-paper{color:var(--navy)}
.spread-copy{position:absolute;font-family:"Roboto Condensed",sans-serif;font-size:10px;line-height:14.5px}
.about-copy{left:33px;top:74px;width:270px;color:var(--white)}
.about-list{list-style:none;margin-top:12px;line-height:15.8px}
.about-list li::before,.services-list li::before,.box li::before{content:"• "}
.services-intro{left:33px;top:343px;width:240px;color:var(--ink);font-weight:700}
.services-intro .lead{font-size:11px;margin-bottom:18px}
.services-list{left:33px;top:437px;width:438px;list-style:none;color:var(--ink)}
.services-list li+li{margin-top:14px}
.spread-foot .url{left:33px;top:12px}
.inner-left .brand{right:30px;top:718px;font-size:24px}
.inner-right .brand{right:30px;top:34px;font-size:26px}
.quality-item{position:absolute;left:33px;width:440px}
.quality-item h3{display:flex;align-items:center;gap:12px;font-family:"Roboto Condensed",sans-serif;font-weight:700;font-size:12px;color:#1b1b22}
.badge{width:28px;height:28px;border-radius:50%;background:var(--navy);display:flex;align-items:center;justify-content:center}
.badge svg{display:block}
.quality-item p{margin-top:6px;font-family:"Roboto Condensed",sans-serif;font-size:9.6px;line-height:12.8px;color:var(--ink)}
.box{position:absolute;top:422px;height:270px;border:1px solid #8a8f99;padding:16px 14px;font-family:"Roboto Condensed",sans-serif;font-size:11.3px;line-height:17.2px;color:#1b1b22}
.box h4{font-weight:700;font-size:11.3px;color:var(--navy)}
.box ul{list-style:none}
.box-fields{left:33px;width:215px}
.box-forms{left:256px;width:212px}
</style>
</head>
<body>

<!-- outer spread, opened flat -->
<div class="outer-shadow"></div>
<div class="outer-spread">
  <section class="page back">
    <div class="back-head">
      <span class="rule"></span>
      <h2>Intro Qorvith</h2>
      <p>Qorvith Global Compounding Pharmacy: The Right Choice<br>The right choice for you and your Patients.</p>
    </div>
    <div class="photo" role="img" aria-label="Close-up of a pharmacy product bottle"></div>
    <svg class="page-geo" width="480" height="700" viewBox="0 0 480 700" aria-hidden="true">
      <polygon points="0,452 395,452 480,250 480,655 0,655" fill="#111f8f"/>
      <polygon points="420,110 480,110 480,200 455,260" fill="#ffffff" opacity=".7"/>
    </svg>
    <div class="intro-copy">
      <p>We believe every person in the world should have access to the best possible health care, which is why we offer a full range of pharmaceuticals at our compounding pharmacy. We know that each person is unique and deserves personalized care—that's why we work with you to create a solution that works for your patient's specific needs. Our pharmacists will work with you to understand your goals and provide a customized plan that will help you reach them. We know what it's like being a doctor today: You have so many responsibilities, so many patients who need your attention... and so many medications that don't always work!</p>
      <p>We know that as a doctor, you have a lot on your plate—and sometimes it can feel like there's no time left in the day to get things done. That's why we work with you directly to develop customized solutions that meet your needs and help you get more done. Whether you need a new drug or an injectable for one of your patients, we're here for you.</p>
      <p>Whether you're looking for something simple or something more complex, we're here to help make sure that everything gets done on time and according to your specifications—and at reasonable prices That's why we created this brochure: To make sure you know about all of the ways we can help.</p>
    </div>
    <div class="contact">
      <div class="contact-icons"><span></span><span></span><span></span></div>
      18 Velomarou street,<br>15344 Pallini, Athens Greece<br>+30 210 5550142<br>hello@qorvith-rx.example
    </div>
    <div class="brand">QORVITH</div>
    <div class="follow">Follow Us <span class="social"></span><span class="social"></span></div>
    <div class="contact-us">CONTACT US</div>
    <footer class="page-foot"><span class="url">www.qorvith-rx.example</span><span class="url-bar"></span></footer>
  </section>

  <section class="page cover">
    <svg class="page-geo" width="480" height="700" viewBox="0 0 480 700" aria-hidden="true">
      <polygon points="0,0 78,0 0,160" fill="#1fbf9b"/>
      <polygon points="92,0 200,0 20,380 0,380 0,190" fill="#111f8f"/>
      <polygon points="480,130 480,450 402,450" fill="#1fbf9b"/>
      <polygon points="0,380 20,380 0,420" fill="#1fbf9b"/>
    </svg>
    <div class="photo" role="img" aria-label="Pharmacist in cleanroom gear handling a capsule filling tray"></div>
    <div class="brand">QORVITH</div>
    <div class="cover-band">
      <h1 class="cover-title"><span class="accent">Qorvith Global</span><br>Compounding Pharmacy</h1>
      <p class="tagline">The Right Choice The right choice for you and your Patients.</p>
    </div>
    <footer class="page-foot"><span class="url">www.qorvith-rx.example</span><span class="url-bar"></span></footer>
  </section>
</div>
<p class="caption" style="left:298px">Cover Page</p>
<p class="caption" style="left:810px">Back Page</p>

<!-- cover page -->
<section class="page cover" style="left:107px;top:793px">
  <svg class="page-geo" width="480" height="700" viewBox="0 0 480 700" aria-hidden="true">
    <polygon points="0,0 78,0 0,160" fill="#1fbf9b"/>
    <polygon points="92,0 200,0 20,380 0,380 0,190" fill="#111f8f"/>
    <polygon points="480,130 480,450 402,450" fill="#1fbf9b"/>
    <polygon points="0,380 20,380 0,420" fill="#1fbf9b"/>
  </svg>
  <div class="photo" role="img" aria-label="Pharmacist in cleanroom gear handling a capsule filling tray"></div>
  <div class="brand">QORVITH</div>
  <div class="cover-band">
    <h1 class="cover-title"><span class="accent">Qorvith Global</span><br>Compounding Pharmacy</h1>
    <p class="tagline">The Right Choice The right choice for you and your Patients.</p>
  </div>
  <footer class="page-foot"><span class="url">www.qorvith-rx.example</span><span class="url-bar"></span></footer>
</section>

<!-- back page -->
<section class="page back" style="left:619px;top:793px">
  <div class="back-head">
    <span class="rule"></span>
    <h2>Intro Qorvith</h2>
    <p>Qorvith Global Compounding Pharmacy: The Right Choice<br>The right choice for you and your Patients.</p>
  </div>
  <div class="photo" role="img" aria-label="Close-up of a pharmacy product bottle"></div>
  <svg class="page-geo" width="480" height="700" viewBox="0 0 480 700" aria-hidden="true">
    <polygon points="0,452 395,452 480,250 480,655 0,655" fill="#111f8f"/>
    <polygon points="420,110 480,110 480,200 455,260" fill="#ffffff" opacity=".7"/>
  </svg>
  <div class="intro-copy">
    <p>We believe every person in the world should have access to the best possible health care, which is why we offer a full range of pharmaceuticals at our compounding pharmacy. We know that each person is unique and deserves personalized care—that's why we work with you to create a solution that works for your patient's specific needs. Our pharmacists will work with you to understand your goals and provide a customized plan that will help you reach them. We know what it's like being a doctor today: You have so many responsibilities, so many patients who need your attention... and so many medications that don't always work!</p>
    <p>We know that as a doctor, you have a lot on your plate—and sometimes it can feel like there's no time left in the day to get things done. That's why we work with you directly to develop customized solutions that meet your needs and help you get more done. Whether you need a new drug or an injectable for one of your patients, we're here for you.</p>
    <p>Whether you're looking for something simple or something more complex, we're here to help make sure that everything gets done on time and according to your specifications—and at reasonable prices That's why we created this brochure: To make sure you know about all of the ways we can help.</p>
  </div>
  <div class="contact">
    <div class="contact-icons"><span></span><span></span><span></span></div>
    18 Velomarou street,<br>15344 Pallini, Athens Greece<br>+30 210 5550142<br>hello@qorvith-rx.example
  </div>
  <div class="brand">QORVITH</div>
  <div class="follow">Follow Us <span class="social"></span><span class="social"></span></div>
  <div class="contact-us">CONTACT US</div>
  <footer class="page-foot"><span class="url">www.qorvith-rx.example</span><span class="url-bar"></span></footer>
</section>

<!-- inner spread -->
<div class="inner-spread">
  <section class="page inner-left">
    <div class="photo about-photo" role="img" aria-label="Lab technician in protective gown using a pipette"></div>
    <div class="about-block"></div>
    <h2 class="section-title on-navy" style="left:33px;top:30px">About Qorvith</h2>
    <div class="spread-copy about-copy">
      <p>Qorvith has been practicing functional medicine for 16 years, offering customized medicine &amp; well-being to 10,000+ customers in more than 30 countries around the world.</p>
      <ul class="about-list">
        <li>Strictly high-quality pharmaceutical ingredients</li>
        <li>Low prices &amp; price match</li>
        <li>Fast turnaround &amp; delivery</li>
        <li>Excellent customer service</li>
        <li>Online platform for free &amp; easy prescription transfer</li>
        <li>Consultation with an expert pharmacist</li>
        <li>State-of-art compounding pharmacy</li>
      </ul>
    </div>
    <div class="photo services-photo" role="img" aria-label="Gloved hand holding a sealed medication package"></div>
    <h2 class="section-title on-paper" style="left:33px;top:292px">Our Services</h2>
    <div class="spread-copy services-intro">
      <p class="lead">Our services for physicians include:</p>
      <p>Customized formulations for all your patient's needs<br>Personalized solutions based on your patient's unique needs<br>Expert advice on how to use our formulations effectively</p>
    </div>
    <ul class="spread-copy services-list">
      <li>We are constantly looking at new technologies and products that can help us create customized solutions for you and your patients. Our goal is to make sure every patient gets the right medication at the right time in an easy-to-administer form.</li>
      <li>Our compounding pharmacy uses only the highest quality ingredients, so you don't have to worry about your patients getting a product that won't work as well as it should or having an adverse reaction to it. We know how important it is that your patients feel comfortable with their treatment plan, so we do everything we can to make sure they're getting what they need.</li>
      <li>When you need a prescription, you need it now. That's why we're here—we can get your medicines to you in as little as a few hours.</li>
      <li>Our compounding pharmacy is equipped with the most advanced technology available to ensure that your medicines are always safe and effective. Our team of pharmacists has decades of experience in compounding medications, and they work closely with doctors to make sure that our formulations are tailored specifically to your patient's needs.</li>
    </ul>
    <div class="brand">QORVITH</div>
    <footer class="page-foot spread-foot" style="background:transparent"><span class="url">www.qorvith-rx.example</span><span class="url-bar"></span></footer>
  </section>

  <section class="page inner-right">
    <h2 class="section-title on-paper" style="left:33px;top:30px">Quality</h2>
    <div class="brand">QORVITH</div>
    <div class="quality-item" style="top:70px">
      <h3><span class="badge"><svg width="14" height="14" viewBox="0 0 14 14"><circle cx="7" cy="6" r="4.5" fill="none" stroke="#fff" stroke-width="1.6"/><path d="M4.5 10 3.5 13.5 7 12 10.5 13.5 9.5 10" fill="#fff"/></svg></span>Quality Matters More Than Anything</h3>
      <p>Since day 1, the quality of compounded medications has been our No.1 priority. We apply the highest standards of quality and safety and we inspect and control every stage of the production, from the moment we receive the prescription until it is delivered to the patient.</p>
    </div>
    <div class="quality-item" style="top:157px">
      <h3><span class="badge"><svg width="14" height="14" viewBox="0 0 14 14"><rect x="2.5" y="1.5" width="8" height="11" rx="1" fill="none" stroke="#fff" stroke-width="1.6"/><path d="M4.5 5h4M4.5 8h3" stroke="#fff" stroke-width="1.4"/></svg></span>Extensive Testing Protocols</h3>
      <p>• Continuous tests-both in house and third party- to guarantee the potency, efficacy, and quality of our products. We are one of the only pharmacies in the world to have our own HPLC and Mass Spectrometry capabilities!<br>• Test the quality of all bulk medication materials to assure that they are the best available.</p>
    </div>
    <div class="quality-item" style="top:262px">
      <h3><span class="badge"><svg width="16" height="14" viewBox="0 0 16 14"><circle cx="4" cy="4" r="2" fill="#fff"/><circle cx="8" cy="3.5" r="2.2" fill="#fff"/><circle cx="12" cy="4" r="2" fill="#fff"/><rect x="2.3" y="7" width="3.4" height="6" fill="#fff"/><rect x="6.2" y="6.5" width="3.6" height="6.5" fill="#fff"/><rect x="10.3" y="7" width="3.4" height="6" fill="#fff"/></svg></span>Certified Team</h3>
      <p>• Our team at Qorvith consists of excellent and certified experts, each one in their field. We apply our team to special training programs such as USP 797, USP 800, media fill testing, garbing practices, cleaning and disinfection, and antiseptic practices, etc. that continue throughout the years in order to ensure that we are all up-to-date with the latest standards and practices.</p>
    </div>
    <h2 class="section-title on-paper" style="left:33px;top:380px">Products Information</h2>
    <div class="box box-fields">
      <h4>Compounding specialty fields</h4>
      <ul>
        <li>Anti-Aging</li><li>Hormone replacement for women</li><li>Hormone replacement for men</li><li>Pain Management</li><li>Dermatology</li><li>Sterile Compounding</li><li>Thyroid Imbalance</li><li>Scars and wounds Care</li><li>Pediatrics</li><li>Sports medicine</li><li>Dental</li><li>Veterinary</li>
      </ul>
    </div>
    <div class="box box-forms">
      <h4>What forms do we compound into:</h4>
      <ul>
        <li>Liposomal dermal creams and gels</li><li>Vaginal creams and gels</li><li>Capsules and tablets</li><li>Sublingual lozenges and troches</li><li>Sublingual drops</li><li>Vaginal pessaries</li><li>Suppositories</li><li>Nasal sprays</li><li>Injectables</li><li>Oral Suspensions</li>
      </ul>
    </div>
    <footer class="page-foot spread-foot" style="background:transparent"><span class="url">www.qorvith-rx.example</span><span class="url-bar"></span></footer>
  </section>
</div>

</body>
</html>
```